Garlic Farm for Farm Sales/Restaurant sales

Need a professional, but appealing to agriculture world. We are selling 27 kinds of Organic Garlic from a farm in Simla,CO. I have uploaded logo and business information-we are going to need a template, because I will need to use it for four separate people.
-We are trying to appeal to Farm to table restaurants
-As well as growers/farmers

Target Market(s)

Agriculture Sales/Restaurants-Organic

Industry/Entity Type

Agriculture

Contact Information for Business Card

Want it to look more unique then your average kelto stock card- I want it to look amazing

Font styles to use
Sans Serif

Colors
0455a3
ec1f27
fbed22
ffffff

Requirements
Must have
• Just be creative
Nice to have
• Colorful
Should not have
• plain

```html
<!DOCTYPE html>
<html lang="en">
<head>
<meta charset="utf-8">
<title>Prairie Bulb Garlic — Business Card</title>
<link href="https://fonts.googleapis.com/css2?family=Open+Sans:wght@400;700&display=swap" rel="stylesheet">
<style>
  :root {
    --navy: #0b2f66;
    --red: #c10b2e;
    --ink: #222222;
    --paper: #ffffff;
    --backdrop: #eeeae4;
  }
  * { box-sizing: border-box; margin: 0; padding: 0; }
  html, body { width: 1200px; height: 900px; overflow: hidden; }
  body {
    background: var(--backdrop);
    font-family: "Open Sans", Arial, sans-serif;
    position: relative;
  }
  .card {
    position: absolute;
    width: 560px;
    height: 320px;
    background: var(--paper);
    box-shadow: 0 6px 20px rgba(0,0,0,0.15);
    overflow: hidden;
  }
  .card--front { left: 320px; top: 100px; }
  .card--back  { left: 320px; top: 470px; }

  .brand {
    display: flex;
    align-items: center;
    gap: 12px;
    color: var(--navy);
    font-weight: 700;
    white-space: nowrap;
  }
  .brand__dot {
    border-radius: 50%;
    background: var(--red);
    flex: none;
  }
  .card--front .brand {
    position: absolute;
    left: 0; right: 0; top: 0; bottom: 0;
    justify-content: center;
    font-size: 34px;
  }
  .card--front .brand__dot { width: 34px; height: 34px; }

  .card--back .brand {
    position: absolute;
    right: 28px;
    top: 70px;
    font-size: 22px;
    gap: 9px;
  }
  .card--back .brand__dot { width: 22px; height: 22px; }

  .wave { position: absolute; left: 0; bottom: 0; width: 560px; height: 320px; }

  .holder {
    position: absolute;
    left: 34px;
    top: 32px;
  }
  .holder__name {
    color: var(--red);
    font-weight: 700;
    font-size: 25px;
    line-height: 1.1;
  }
  .holder__role {
    color: var(--ink);
    font-size: 17px;
    margin-top: 4px;
  }
  .contact {
    list-style: none;
    margin-top: 18px;
    font-size: 14.5px;
    color: var(--ink);
    line-height: 1.5;
  }
  .contact li { display: flex; align-items: center; gap: 9px; }
  .contact svg { width: 12px; height: 12px; flex: none; fill: var(--red); }
  .address {
    margin-top: 20px;
    font-size: 14.5px;
    line-height: 1.45;
    color: var(--ink);
    font-style: normal;
  }
</style>
</head>
<body>

  <section class="card card--front" aria-label="Card front">
    <div class="brand"><span class="brand__dot"></span>Prairie Bulb Garlic</div>
  </section>

  <section class="card card--back" aria-label="Card back">
    <svg class="wave" viewBox="0 0 560 320" aria-hidden="true">
      <path d="M0,288 C170,290 300,250 380,196 C430,164 470,150 510,146 L560,146 L560,320 L0,320Z" fill="var(--navy)"/>
      <path d="M0,297 C170,299 305,262 385,210 C440,178 490,170 560,170 L560,320 L0,320Z" fill="var(--paper)"/>
      <path d="M0,303 C170,305 310,270 390,220 C445,188 495,180 560,178 L560,320 L0,320Z" fill="var(--red)"/>
    </svg>

    <div class="brand"><span class="brand__dot"></span>Prairie Bulb Garlic</div>

    <div class="holder">
      <h1 class="holder__name">dale morrow</h1>
      <p class="holder__role">Owner</p>
      <ul class="contact">
        <li><svg viewBox="0 0 12 12"><path d="M1,4 C1,2 3,1 6,1 C9,1 11,2 11,4 L8,5 L8,3.5 L4,3.5 L4,5Z M3,6 L9,6 L10,11 L2,11Z"/></svg>719-555-0142</li>
        <li><svg viewBox="0 0 12 12"><path d="M2,1 L8,1 L8,4 L10,4 L10,11 L2,11Z M4,6 L8,6 L8,7 L4,7Z" fill-rule="evenodd"/></svg>(719)-555-8</li>
        <li><svg viewBox="0 0 12 12"><path d="M0,2 L12,2 L12,10 L0,10Z M1,3 L6,7 L11,3" /></svg>info@prairiebulb.com</li>
        <li><svg viewBox="0 0 12 12"><circle cx="6" cy="6" r="5.5"/></svg>www.prairiebulb.com</li>
      </ul>
      <address class="address">PO Box 218,<br>Simla, CO 80835</address>
    </div>
  </section>

</body>
</html>
```